KRWB new business card design

We need a business card design for our established business which is Australia wide however based in Melbourne. We are a young team of Financial Planners who specialize in Insurance and Basic super advice for people like us.

We are people who help our clients get things done in a timely and cost effective manner whilst having a good time and a laugh along the way.

We would like this to have a consistent feel with our new e-brochure which i have attached from a color and font perspective.

Industry/Entity Type

Business

Requirements
Must have
• We do not need specific address details rather just the states we are in:

VIC/NSW/QLD/TAS
Nice to have
• Curved edge to mate the brochure

```html
<!DOCTYPE html>
<html lang="en">
<head>
<meta charset="utf-8">
<title>KRWB business card</title>
<link rel="stylesheet" href="https://fonts.googleapis.com/css2?family=Roboto+Condensed:wght@400;700&display=swap">
<style>
  :root {
    --page: #e9ebe7;
    --card: #1b221e;
    --card-deep: #141a17;
    --green: #4f9f45;
    --green-dark: #3c7f36;
    --lime: #9ccb45;
    --white: #ffffff;
    --muted: #e4e9e2;
  }
  * { margin: 0; padding: 0; box-sizing: border-box; }
  html, body {
    width: 1200px; height: 900px; overflow: hidden;
    background: var(--page);
    font-family: "Roboto Condensed", Arial, sans-serif;
  }
  .sheet {
    width: 1200px; height: 900px;
    display: flex; flex-direction: column; align-items: center;
    justify-content: center; gap: 44px;
  }
  .card {
    position: relative;
    width: 680px; height: 388px;
    border-radius: 6px;
    background: radial-gradient(ellipse at 45% 40%, var(--card) 0%, var(--card-deep) 100%);
    box-shadow: 0 6px 18px rgba(0,0,0,0.18);
    overflow: hidden;
  }
  .card-lines { position: absolute; inset: 0; }

  /* front */
  .front-brand {
    position: absolute; left: 150px; top: 150px;
    display: flex; align-items: center; gap: 26px;
  }
  .brand-square {
    width: 96px; height: 96px; border-radius: 14px;
    background: var(--lime);
  }
  .front-brand .brand-name {
    color: var(--white); font-weight: 700;
    font-size: 38px; line-height: 1.02; letter-spacing: 0.5px;
  }

  /* back */
  .back-brand {
    position: absolute; left: 232px; top: 102px;
    display: flex; align-items: center; gap: 12px;
  }
  .back-brand .brand-square { width: 48px; height: 48px; border-radius: 8px; }
  .back-brand .brand-name {
    color: var(--white); font-weight: 700;
    font-size: 21px; line-height: 1.05;
  }
  .contact {
    position: absolute; right: 44px; top: 128px;
    text-align: right; color: var(--muted);
    font-size: 17px; line-height: 1.75; list-style: none;
  }
  .states {
    position: absolute; left: 80px; top: 262px;
    color: var(--muted); font-size: 15px; line-height: 1.25;
    list-style: none; letter-spacing: 0.3px;
  }
</style>
</head>
<body>
<main class="sheet">

  <section class="card card-front" aria-label="Card front">
    <svg class="card-lines" viewBox="0 0 680 388" aria-hidden="true">
      <rect x="62" y="18" width="588" height="340" rx="62" fill="none" stroke="var(--green)" stroke-width="14"/>
      <rect x="0" y="104" width="680" height="14" fill="var(--lime)" opacity="0.55"/>
    </svg>
    <div class="front-brand">
      <span class="brand-square"></span>
      <p class="brand-name">kindred<br>wealth builders</p>
    </div>
  </section>

  <section class="card card-back" aria-label="Card back">
    <svg class="card-lines" viewBox="0 0 680 388" aria-hidden="true">
      <rect x="22" y="22" width="636" height="344" rx="30" fill="none" stroke="var(--green)" stroke-width="4"/>
      <line x1="0" y1="56" x2="680" y2="56" stroke="var(--lime)" stroke-width="4" opacity="0.8"/>
    </svg>
    <div class="back-brand">
      <span class="brand-square"></span>
      <p class="brand-name">kindred<br>wealth builders</p>
    </div>
    <ul class="contact">
      <li>1300 555 019</li>
      <li>admin@krwb.com.au</li>
      <li>www.kindredwealthbuilders.com.au</li>
    </ul>
    <ul class="states">
      <li>TASMANIA</li>
      <li>VICTORIA</li>
      <li>GOLD COAST</li>
      <li>NEW SOUTH WALES</li>
    </ul>
  </section>

</main>
</body>
</html>
```